Business Card Design for Training Business

Clear Path Coaching is a new business that delivers training and other services with a focus on topics related to mental health and wellbeing, for example, Wellmind Response Course, Resilience etc. We have a strong focus on evidence-based psychology and neuroscience. I have a logo which I will upload with the brief, so please consider colours that work well with the logo.
Target Market(s)
Adults, workplaces (particularly government and not-for-profits)
Industry/Entity Type
Business
Contact Information for Business Card
Head Strong TrainingSamantha SellwoodDirector0438 770 850sam@headstrongtraining.com.auwww.headstrongtraining.com.au

```html
<!DOCTYPE html>
<html lang="en">
<head>
<meta charset="utf-8">
<title>Clear Path Coaching – Business Card</title>
<link rel="stylesheet" href="https://fonts.googleapis.com/css2?family=Questrial&display=swap">
<style>
  :root {
    --backdrop: #3a3a3a;
    --card-white: #f7f7f7;
    --teal: #20b6bd;
    --brown: #5a4641;
    --ink-grey: #6b6b6b;
    --white: #ffffff;
  }
  * { box-sizing: border-box; margin: 0; padding: 0; }
  html, body {
    width: 1200px; height: 750px; overflow: hidden;
    background: var(--backdrop);
    font-family: "Questrial", "Century Gothic", sans-serif;
  }
  .card {
    position: absolute;
    left: 371px;
    width: 461px;
    height: 262px;
    border-radius: 13px;
    overflow: hidden;
  }
  .card--front { top: 106px; background: var(--card-white); }
  .card--back  { top: 387px; background: var(--teal); }

  .front-curve { position: absolute; left: 0; top: 0; width: 461px; height: 262px; }

  .brand-mark {
    position: absolute; left: 50%; top: 17px;
    width: 70px; height: 70px; margin-left: -35px;
    border-radius: 50%;
    border: 2px solid var(--teal);
  }
  .brand-name {
    position: absolute; left: 0; right: 0; top: 100px;
    text-align: center;
    font-size: 19px; letter-spacing: 2.5px;
    color: var(--ink-grey);
    text-transform: uppercase;
  }

  .person {
    position: absolute; left: 0; right: 0; top: 176px;
    text-align: center; color: var(--white);
  }
  .person__name { font-size: 19px; line-height: 22px; letter-spacing: 0.3px; }
  .person__role { font-size: 13.5px; line-height: 18px; }

  .contacts {
    position: absolute; left: 0; right: 0; top: 218px;
    text-align: center; color: var(--white);
    font-size: 12px; line-height: 18px;
  }
  .contacts__row { display: flex; justify-content: center; gap: 16px; }
  .contacts__item { display: inline-flex; align-items: center; gap: 5px; }
  .contacts__item svg { width: 11px; height: 11px; fill: var(--white); }

  .back-mark {
    position: absolute; left: 50%; top: 60px;
    width: 90px; height: 90px; margin-left: -45px;
    border-radius: 50%;
    border: 2px solid var(--white);
  }
  .back-name {
    position: absolute; left: 0; right: 0; top: 164px;
    text-align: center; color: var(--white);
    font-size: 13px; letter-spacing: 1.5px; text-transform: uppercase;
  }
  .back-web {
    position: absolute; left: 0; right: 0; top: 226px;
    text-align: center; color: var(--white); font-size: 12.5px;
  }
</style>
</head>
<body>
  <section class="card card--front">
    <svg class="front-curve" viewBox="0 0 461 262" aria-hidden="true">
      <path d="M0 196 Q230.5 115 461 196 L461 262 L0 262 Z" fill="var(--teal)"/>
      <path d="M0 207 Q230.5 125 461 207" fill="none" stroke="var(--brown)" stroke-width="3"/>
    </svg>
    <div class="brand-mark"></div>
    <div class="brand-name">Clear Path Coaching</div>

    <div class="person">
      <div class="person__name">Rebecca Tanfield</div>
      <div class="person__role">Director</div>
    </div>

    <div class="contacts">
      <div class="contacts__row">
        <span class="contacts__item">
          <svg viewBox="0 0 24 24"><path d="M6.6 10.8a15.1 15.1 0 0 0 6.6 6.6l2.2-2.2a1 1 0 0 1 1-.25 11.4 11.4 0 0 0 3.6.57 1 1 0 0 1 1 1V20a1 1 0 0 1-1 1A17 17 0 0 1 3 4a1 1 0 0 1 1-1h3.5a1 1 0 0 1 1 1c0 1.25.2 2.45.57 3.57a1 1 0 0 1-.25 1z"/></svg>
          0491 362 517
        </span>
        <span class="contacts__item">
          <svg viewBox="0 0 24 24"><path d="M2 5h20v14H2z M2 5l10 8 10-8"/></svg>
          bec@clearpathcoaching.example.au
        </span>
      </div>
      <div class="contacts__row">
        <span class="contacts__item">
          <svg viewBox="0 0 24 24"><circle cx="12" cy="12" r="10"/></svg>
          www.clearpathcoaching.example.au
        </span>
      </div>
    </div>
  </section>

  <section class="card card--back">
    <div class="back-mark"></div>
    <div class="back-name">Clear Path Coaching</div>
    <div class="back-web">www.clearpathcoaching.example.au</div>
  </section>
</body>
</html>
```